Summer Sunglass offer

Need a poster design for a spring / summer campaign. We are an opticians with good footfall. The design needs to be eye catching and aimed at 40 year old plus. The offer is Up to 50% off sunglass offer, t&c apply. (I have attached our last year campaign)
Also need a 2 sided A5 leaflet design (see attached)
I've uploaded a copy of our logo

A5 leaflet should read:

Grab a bargain on two great looks this summer Upto 50% off sunglasses
Look great and stay safe in the sun this summer

We want you to look great, feel fantastic and most of all stay safe in the sun this summer. That’s why we’re offering you 50% off prescription sunglasses with every complete pair of glasses you buy this summer or 25% off for prescription sunglasses with no other purchase.
Find you new summer looks from our gorgeous collection of frames in store. It matters to us that you look great in your new glasses as much as how well you see through them, so we’ll be on hand to help you find frames that suit you best.
What new looks will you go for? Smart or sassy? Formal or Fun? Whatever you’re in the mood for, you’ll find it in our collections this summer.
Call in today to find your new looks, and remember to bring your prescription if you don’t need an eye test.

Target Market(s)

40 + year old

Industry/Entity Type

Optician

Colors

Designer to choose colors to be used in the design.

Requirements
Must have
• Images, preferably a male and Female image

```html
<!DOCTYPE html>
<html lang="en">
<head>
<meta charset="utf-8">
<title>Brookfield Eyecare Centre – Summer Sunglasses Offer</title>
<link href="https://fonts.googleapis.com/css2?family=Lato:wght@300;400;700;900&display=swap" rel="stylesheet">
<style>
  :root {
    --teal: #4fe0d0;
    --teal-light: #86f2e6;
    --teal-mid: #5de8d6;
    --royal: #1a3cf0;
    --logo-blue: #2a4fd8;
    --red: #ee1c1c;
    --ring: #6ff0bf;
    --ink: #1b1b1b;
    --white: #ffffff;
    --sand: #efe7dc;
  }
  * { box-sizing: border-box; margin: 0; padding: 0; }
  html, body { width: 846px; height: 1200px; overflow: hidden; background: var(--white); }
  body { font-family: "Lato", sans-serif; color: var(--ink); }

  .poster { position: relative; width: 846px; height: 1200px; overflow: hidden; background: var(--white); }

  .hero {
    position: absolute; left: 0; top: 0; width: 846px; height: 572px;
    background: linear-gradient(100deg, var(--teal) 0%, var(--teal-mid) 45%, var(--teal-light) 100%);
  }
  .hero-photo {
    position: absolute; left: 394px; top: 0; width: 452px; height: 572px;
    background: radial-gradient(ellipse at 55% 35%, #e9d3b8 0%, #d59b6a 28%, rgba(240,185,70,0.9) 58%, rgba(134,242,230,0) 80%);
  }
  .hero-rule { position: absolute; left: 0; top: 572px; width: 846px; height: 10px; background: var(--royal); }

  .brand-tab {
    position: absolute; left: 34px; top: 0; width: 374px; height: 102px;
    background: var(--white); border-radius: 0 0 26px 26px;
    display: flex; align-items: center; gap: 12px; padding-left: 36px;
  }
  .brand-dot { width: 22px; height: 22px; border-radius: 50%; background: var(--teal); flex: none; }
  .brand-name { font-weight: 700; color: var(--logo-blue); font-size: 19px; line-height: 1.15; letter-spacing: 1.5px; }

  .headline { position: absolute; left: 34px; top: 128px; color: var(--white); }
  .headline-lead { font-weight: 300; font-size: 37px; line-height: 48px; letter-spacing: 0; }
  .headline-main { font-weight: 900; font-size: 36px; line-height: 49px; letter-spacing: 2.6px; }
  .headline-tail { font-weight: 900; font-size: 35px; line-height: 49px; letter-spacing: -0.9px; }
  .headline-sub { font-weight: 400; font-size: 19px; line-height: 26px; margin-top: 6px; }

  .badge-flora { position: absolute; border-radius: 50%; background: radial-gradient(circle, #f0a8e6 0%, #c8f0d8 60%, rgba(255,255,255,0) 75%); }
  .badge-flora.left { left: 36px; top: 350px; width: 100px; height: 170px; }
  .badge-flora.right { left: 308px; top: 390px; width: 86px; height: 130px; }

  .offer-badge {
    position: absolute; left: 105px; top: 331px; width: 220px; height: 220px;
    border-radius: 50%; background: var(--white);
  }
  .offer-badge::before {
    content: ""; position: absolute; left: 11px; top: 11px; right: 11px; bottom: 11px;
    border-radius: 50%; border: 3px solid var(--ring);
  }
  .offer-text { position: absolute; left: 0; top: 0; width: 100%; height: 100%; }
  .offer-upto { position: absolute; left: 44px; top: 40px; color: var(--royal); font-weight: 900; font-size: 30px; letter-spacing: -0.5px; }
  .offer-figure { position: absolute; left: 36px; top: 66px; color: var(--red); font-weight: 900; font-size: 80px; line-height: 80px; letter-spacing: -2px; }
  .offer-figure .pct { font-size: 46px; margin-left: 10px; }
  .offer-item { position: absolute; left: 36px; top: 140px; color: var(--royal); font-weight: 900; font-size: 26px; letter-spacing: -0.8px; }

  .backdrop {
    position: absolute; left: 0; top: 582px; width: 846px; height: 618px;
    background: linear-gradient(180deg, var(--white) 0%, #fbf9f6 35%, #d9d3cb 62%, var(--sand) 100%);
  }

  .copy { position: absolute; left: 70px; top: 622px; width: 710px; font-size: 19px; line-height: 30px; }
  .copy p { margin-bottom: 15px; }
  .copy .cta { color: var(--royal); font-weight: 700; font-size: 22px; line-height: 36px; margin-top: 2px; }

  .web-bar { position: absolute; top: 1051px; height: 51px; }
  .web-bar.block-left { left: 0; width: 51px; background: var(--royal); }
  .web-bar.block-right { left: 795px; width: 51px; background: var(--royal); }
  .web-bar.url {
    left: 72px; width: 696px; background: var(--teal);
    color: var(--white); font-weight: 700; font-size: 27px; display: flex; align-items: center; justify-content: center;
  }

  .terms { position: absolute; left: 78px; top: 1114px; width: 684px; font-size: 12.6px; line-height: 25px; letter-spacing: 0.2px; }
  .terms-line { display: block; white-space: nowrap; }
  .terms-line.spread { white-space: normal; text-align: justify; text-align-last: justify; }
</style>
</head>
<body>
<div class="poster">
  <section class="hero">
    <div class="hero-photo" role="img" aria-label="Smiling woman in a straw sun hat, dark sunglasses and a yellow jumper"></div>

    <div class="brand-tab">
      <span class="brand-dot"></span>
      <div class="brand-name">BROOKFIELD<br>EYECARE CENTRE</div>
    </div>

    <div class="headline">
      <h1 class="headline-lead">GRAB A BARGAIN ON</h1>
      <div class="headline-main">TWO GREAT LOOKS</div>
      <div class="headline-tail">FOR THE PRICE OF ONE.</div>
      <p class="headline-sub">Look great and stay safe in the sun this season</p>
    </div>

    <div class="badge-flora left" role="img" aria-label="Pink flowers and leaves"></div>
    <div class="badge-flora right" role="img" aria-label="Pink flower and leaves"></div>
    <div class="offer-badge">
      <div class="offer-text">
        <span class="offer-upto">UP TO</span>
        <span class="offer-figure">50<span class="pct">%</span></span>
        <span class="offer-item">SUNGLASSES</span>
      </div>
    </div>
  </section>
  <div class="hero-rule"></div>

  <div class="backdrop" role="img" aria-label="Faded pair of sunglasses resting on sand"></div>

  <main class="copy">
    <p>We want you to look great, feel fantastic and most of all stay safe in the sun this summer. That’s why we’re offering you 50% off prescription sunglasses with every complete pair of glasses you buy this summer, or 25% off prescription sunglasses with no other purchase.</p>
    <p>Find your new summer looks from our gorgeous collection of frames in store. It matters to us that you look great in your new glasses as much as how well you see through them, so we’ll be on hand to help you find frames that suit you best.</p>
    <p>What new looks will you go for? Smart or sassy? Formal or Fun? Whatever you’re in the mood for, you’ll find it in our collections this summer.</p>
    <p class="cta">Call in today to find your new looks, and remember to bring your prescription if you don’t need an eye test.</p>
  </main>

  <div class="web-bar block-left"></div>
  <div class="web-bar url">www.brookfieldeyecare.co.uk</div>
  <div class="web-bar block-right"></div>

  <p class="terms">
    <span class="terms-line spread">*Offer includes frame from selected range, standard single vision lenses, tint and uv protection.</span>
    <span class="terms-line">Lens upgrades available at extra cost. Offer excludes Solvane frames. Cannot be used with any other offer.</span>
  </p>
</div>
</body>
</html>
```